Web Design Project for a Software & Consulting Company

We have just completed a recent ArtHerdly project for a new logo (see attached).
As the next stage of our rebranding we now require a website re-design to complement the new logo.
Our current site, http://www.corvinsoft.example was built in-house and does not come across as professional as we would like. We supply software and associated services to some of the world’s largest oil companies and we need our site to reflect that level of client.
We will also be posting another design project for brochures, PowerPoint slides and other materials very soon.
We would like designs for…
Home page
Product page
• TZQ
• BLV
• PNJ
Services
News page
About Us page
Contact Us page
Page for mobile devices that gives basic company and product information
Currently the site is small but we intend to increase content to include white papers etc. this should be taken into account when designing the navigation therefore we would prefer navigation through styled text links rather than images.
Colour schemes should broadly be taken from our new logo, where the dark blue and dark green from the left and right sides of the logo are the main colours, but other, brighter accent colours can be used to highlight sections or content.
Dark Blue = C:88, M:55, Y:44, K:28
Dark Green = C:87, M:53, Y:50, K:50
NB: Don’t use the logo on our current site, make sure you use the one attached.
We would prefer the final file format to be a layered PSD.
The site should be clean and professional and communicate the following...
• That we have a great depth and breadth of knowledge about our customers’ business, enabling us to deliver the best systems and solutions.
• That we are a leading provider of cost estimation and control solutions to the oil and gas industry.
• The benefits of our software and consulting services.
• Show that we deliver outstanding customer service and value with a very high level of professionalism
• The site should have no Flash and be able to self-adjust to fit any screen size.
Things to avoid …
• Obvious and clichéd oil industry imagery, no oil rigs
• Cartoon style graphics
Our Background
We are an integrated software and consulting organization specialising in the drilling side of the oil and gas industry. Simply put our software helps companies better understand, predict and communicate the cost of drilling wells.
We have 3 software products and a consulting offering consisting of…
• TZQ - Probabilistic time and cost software
• BLV – Cost tracking and reporting software
• PNJ – (currently known as DrillSavant) – Lessons learned software
• Consulting services
Our systems are in use in over 30 countries with a broad range of clients including: GN, Marovel, Dunt, Koruna, VELO Sirkami, FALUMI and Quintex.
Our current site can be found at www.corvinsoft.example
Our main competitors are
• http://www.drovanic.example/
• http://www.sumbrask.example/
• http://www.kve.example/services/software-solutions/p1-
Our depth of drilling knowledge, quality of software and collaboration with clients differentiate us form the competition.
We strive for very high levels of customer service.
We look forward to receiving your designs!
Updates
Thanks to all the designers who have submitted a design, we appreciate the effort.
We will do our best to give individual feedback on each design but given that many are quite similar we thought we would give some general feedback first.
Nearly all the designs submitted so far have been slight variations on…
-
Top Menu
-
Scrolling Photo Banner
-
4 Columns
-
Body
-
Deep Footer
These designs are well executed but they are basically the same layout as our existing site and while there is nothing inherently wrong with this layout we would like to see some designs that are a bit more innovative and different. We don’t really want just a polished version of our current site.
Thanks again,
CVS
Thanks to everyone who has submitted a design, the response has been great.
We are close to making a decision so if you are intending to submit a design please do it soon, the deadline is only a few days away.
Thanks again.
CVS
Target Market(s)
Mid to high level executives
Industry/Entity Type
Oil And Gas
Look and feel

```html
<!DOCTYPE html>
<html lang="en">
<head>
<meta charset="utf-8">
<title>Corvin Soft Technologies – Home</title>
<link rel="stylesheet" href="https://fonts.googleapis.com/css2?family=Ubuntu:wght@300;400;500;700&display=swap">
<style>
:root{
  --blue:#2f6377;
  --blue-dark:#26586b;
  --green:#4e6a3d;
  --badge:#566b4b;
  --page:#e8e8e8;
  --nav:#444444;
  --footer:#484848;
  --footer-base:#343434;
  --text:#555555;
  --muted:#8a8a8a;
  --panel:#f6f6f6;
  --line:#d2d2d2;
}
*{box-sizing:border-box;margin:0;padding:0}
html,body{width:1021px;height:1200px;overflow:hidden}
body{background:var(--page);font-family:"Ubuntu",sans-serif;color:var(--text);position:relative;border-top:4px solid #2b4f5c}
.site{position:absolute;left:59px;top:0;width:907px;height:1200px;background:#fff}
.abs{position:absolute}

/* header */
.brand{left:10px;top:22px;display:flex;align-items:center;gap:12px}
.brand-dot{width:46px;height:46px;border-radius:50%;background:var(--blue)}
.brand-name{font-size:26px;font-weight:700;color:var(--blue);line-height:1}
.brand-sub{font-size:12px;letter-spacing:4px;color:var(--blue);margin-top:4px}
.contact-line{right:15px;top:53px;font-size:13px;color:var(--blue)}
.social{right:12px;top:79px;display:flex;gap:3px}
.social span{width:29px;height:29px;background:#6d6d6d;border:1px solid #9a9a9a;box-shadow:1px 2px 2px rgba(0,0,0,.25)}

/* nav */
.nav{left:0;top:123px;width:907px;height:50px;background:var(--nav)}
.nav-item{top:0;height:50px;display:flex;align-items:center;gap:10px;color:#f2f2f2;font-size:17px}
.nav-item.active{background:var(--blue);left:0;width:136px;padding-left:28px}
.nav-item svg{fill:#8c8c8c}
.nav-item.active svg{fill:#cfe0e6}
.nav-sep{top:13px;width:1px;height:25px;background:#5a5a5a}

/* hero */
.hero-photo{left:82px;top:188px;width:430px;height:305px;background:linear-gradient(90deg,#1f2430 0%,#3b3f4a 30%,#c9cdd3 55%,#eef0f2 85%,#fff 100%)}
.slide-btn{top:312px;width:54px;height:54px;border-radius:50%;background:#f1f1f1;display:flex;align-items:center;justify-content:center}
.headline{left:400px;top:272px;width:420px;text-align:center;font-size:34px;font-weight:300;color:var(--blue);line-height:43px;white-space:nowrap}
.headline b{font-weight:400;color:var(--green)}

/* features */
.features{left:0;top:493px;width:907px;height:227px;background:var(--panel);border-top:1px dashed var(--line);border-bottom:1px dashed var(--line)}
.card{top:72px;width:212px;height:150px;background:#fff;border:1px solid #cfcfcf;padding:5px 7px}
.card h3{font-size:22px;font-weight:400;color:var(--blue);line-height:24px}
.card h4{font-size:17px;font-weight:400;color:var(--green);line-height:20px}
.card p{font-size:12px;color:var(--muted);line-height:15px;margin-top:3px}
.card .more{position:absolute;right:8px;bottom:3px;font-size:12px;color:#333}
.badge-icon{top:8px;width:88px;height:88px;border-radius:50%;background:#fff;border:3px solid var(--blue);box-shadow:inset 0 0 0 4px #fff,inset 0 0 0 5px #d8d8d8;display:flex;align-items:center;justify-content:center}

/* about */
.section-title{font-size:20px;font-weight:400;color:#333}
.about-text{left:12px;top:787px;width:570px;font-size:12px;line-height:15px;color:var(--text)}
.about-text p+p{margin-top:14px}
.partner{left:610px;top:758px;width:282px;height:112px;background:var(--badge);border:1px solid #3a4a33;border-radius:8px}

/* clients */
.clients{left:0;top:915px;width:907px;height:56px;border:1px solid #cfcfcf;background:#fff}
.clients-arrow{top:13px;width:29px;height:28px;background:#b1b1b1;display:flex;align-items:center;justify-content:center}
.client{top:14px;font-size:24px;font-weight:700;line-height:28px}

/* footer */
.footer{left:0;top:990px;width:907px;height:183px;background:var(--footer);border-top:5px solid var(--footer-base)}
.region h2{font-size:24px;font-weight:400;color:#fff}
.region ul{list-style:none;margin-top:15px}
.region li{font-size:11px;color:#eee;width:150px;border-bottom:1px dotted #8a8a8a;padding-bottom:4px;margin-bottom:7px;white-space:nowrap}
.divider{left:505px;top:30px;width:2px;height:130px;background:#3c3c3c}
.feedback h2{font-size:17px;font-weight:400;color:#fff;line-height:20px}
.field{background:#3a3a3a;border:1px solid #5a5a5a;border-radius:3px;font-size:11px;color:#8c8c8c;padding:6px 10px}
.base{left:0;top:1173px;width:907px;height:27px;background:var(--footer-base);display:flex;align-items:center;padding:0 14px 0 29px;font-size:11px;color:#eee}
.base a{color:#eee;text-decoration:none;margin-right:16px}
.base .copy{margin-left:auto;color:#bbb}
</style>
</head>
<body>
<div class="site">

  <header>
    <div class="abs brand">
      <span class="brand-dot"></span>
      <div>
        <div class="brand-name">CORVIN SOFT</div>
        <div class="brand-sub">TECHNOLOGIES</div>
      </div>
    </div>
    <div class="abs contact-line">Contact Us: +44(0)1632 96041</div>
    <div class="abs social"><span></span><span></span><span></span><span></span><span></span><span></span></div>
  </header>

  <nav class="abs nav">
    <a class="abs nav-item active">
      <svg width="24" height="22" viewBox="0 0 24 22"><path d="M12 1 1 11h3v10h6v-6h4v6h6V11h3z"/></svg>Home</a>
    <a class="abs nav-item" style="left:158px">
      <svg width="24" height="22" viewBox="0 0 24 22"><path d="M2 2h18v18H2zM5 5v4h6V5zm8 0v2h5V5zm0 4v2h5V9zM5 12v2h13v-2zm0 4v2h13v-2z" fill-rule="evenodd"/></svg>News</a>
    <span class="abs nav-sep" style="left:343px"></span>
    <a class="abs nav-item" style="left:315px;padding-left:60px">
      <svg width="20" height="22" viewBox="0 0 20 22"><circle cx="10" cy="6" r="5"/><path d="M1 21c0-6 4-9 9-9s9 3 9 9z"/></svg>About Us</a>
    <span class="abs nav-sep" style="left:510px"></span>
    <a class="abs nav-item" style="left:528px">
      <svg width="24" height="24" viewBox="0 0 24 24"><path d="M3 20 14 9l2 2L5 22zM15 3l6 6-3 1-4-4z"/><path d="M4 4l4 1 12 12-2 2L6 7z"/></svg>Solutions</a>
    <span class="abs nav-sep" style="left:671px"></span>
    <a class="abs nav-item" style="left:690px;gap:4px">
      <svg width="24" height="26" viewBox="0 0 24 26"><path d="M5 2 9 7 6 10c1 4 4 7 8 9l3-3 5 4-3 4C10 23 2 14 1 5z"/></svg>Contact Us</a>
  </nav>

  <section class="hero">
    <div class="abs hero-photo" role="img" aria-label="Photo of a smiling businesswoman with arms folded in front of a blurred group of business people"></div>
    <div class="abs slide-btn" style="left:19px">
      <svg width="18" height="28" viewBox="0 0 18 28"><path d="M15 2 4 14l11 12" fill="none" stroke="#555" stroke-width="5"/></svg>
    </div>
    <div class="abs slide-btn" style="left:836px">
      <svg width="18" height="28" viewBox="0 0 18 28"><path d="M3 2l11 12L3 26" fill="none" stroke="#555" stroke-width="5"/></svg>
    </div>
    <h1 class="abs headline">DrillSavant <b>Knowledge</b><br>Lessons <b>Learned</b> for the<br><b>OIL &amp; GAS</b> Industry.</h1>
  </section>

  <section class="abs features">
    <article class="abs card" style="left:8px">
      <h3>Plan</h3><h4>Time &amp; Cost Estimation</h4>
      <p>TZQ delivers a standardized, systematic approach to understanding, quantifying and communicating the impact of project risk to all stakeholders.</p>
      <a class="more">Read More</a>
    </article>
    <article class="abs card" style="left:234px">
      <h3>Execute</h3><h4>Materials &amp; Cost Control</h4>
      <p>Since 1992 BLV has been helping companies optimize their materials and logistics processes and accurately track costs on a daily basis.</p>
      <a class="more">Read More</a>
    </article>
    <article class="abs card" style="left:460px">
      <h3>Learn</h3><h4>Lesson Learned</h4>
      <p>DrillSavant is an advanced lessons learned and knowledge management system for use in the Oil &amp; Gas industry. It's fully searchable and easy to use.</p>
      <a class="more">Read More</a>
    </article>
    <article class="abs card" style="left:686px">
      <h3>Embed</h3><h4>Services &amp; Consulting</h4>
      <p>Software solutions rely on people and processes to deliver results. From analysis through execution we support our clients to improve performance.</p>
      <a class="more">Read More</a>
    </article>

    <div class="abs badge-icon" style="left:110px">
      <svg width="48" height="54" viewBox="0 0 48 54" fill="var(--green)"><circle cx="24" cy="24" r="11"/><rect x="19" y="33" width="10" height="12" rx="2"/><path d="M24 3v7M7 10l5 5M41 10l-5 5M2 26h7M46 26h-7" stroke="var(--green)" stroke-width="3"/></svg>
    </div>
    <div class="abs badge-icon" style="left:336px">
      <svg width="46" height="50" viewBox="0 0 46 50"><rect x="4" y="3" width="38" height="44" rx="6" fill="none" stroke="var(--green)" stroke-width="5"/><path d="M13 16h20M13 25h20M13 34h20" stroke="var(--green)" stroke-width="4"/></svg>
    </div>
    <div class="abs badge-icon" style="left:562px">
      <svg width="56" height="56" viewBox="0 0 56 56" fill="var(--green)"><rect x="13" y="17" width="30" height="22" rx="3" fill="none" stroke="var(--green)" stroke-width="4"/><rect x="13" y="17" width="30" height="6"/><path d="M28 2l6 7H22zM28 54l6-7H22zM2 28l7-6v12zM54 28l-7-6v12z"/></svg>
    </div>
    <div class="abs badge-icon" style="left:788px">
      <svg width="44" height="54" viewBox="0 0 44 54" fill="var(--green)"><rect x="2" y="2" width="40" height="50" rx="6"/><rect x="8" y="8" width="28" height="10" fill="#fff"/><g fill="#fff"><rect x="8" y="23" width="7" height="6"/><rect x="18.5" y="23" width="7" height="6"/><rect x="29" y="23" width="7" height="6"/><rect x="8" y="33" width="7" height="6"/><rect x="18.5" y="33" width="7" height="6"/><rect x="29" y="33" width="7" height="6"/><rect x="8" y="42" width="7" height="5"/><rect x="18.5" y="42" width="7" height="5"/><rect x="29" y="42" width="7" height="5"/></g></svg>
    </div>
  </section>

  <section class="about">
    <h2 class="abs section-title" style="left:12px;top:738px">About Us</h2>
    <div class="abs about-text">
      <p>Corvin Soft Technologies have developed and continue to support software in over 30 countries, providing real results to hundreds of drilling operations.</p>
      <p>With decades of hands-on software and well engineering experience, we are uniquely positioned to provide the right solution to our customers.</p>
    </div>
    <div class="abs partner" role="img" aria-label="Software partner badge"></div>
  </section>

  <section class="our-clients">
    <h2 class="abs section-title" style="left:16px;top:884px;color:var(--blue)">Our Clients</h2>
    <div class="abs clients">
      <div class="abs clients-arrow" style="left:0">
        <svg width="10" height="14" viewBox="0 0 10 14"><path d="M8 1 2 7l6 6" fill="none" stroke="#fff" stroke-width="3"/></svg>
      </div>
      <span class="abs client" style="left:98px;color:#1d6b3f">Dunt</span>
      <span class="abs client" style="left:190px;color:#c9a227">Koruna</span>
      <span class="abs client" style="left:330px;color:#3d8d2a">GN</span>
      <span class="abs client" style="left:386px;color:#2357a6">Marovel</span>
      <span class="abs client" style="left:512px;color:#222">FALUMI</span>
      <span class="abs client" style="left:645px;color:#b06e12">VELO</span>
      <span class="abs client" style="left:730px;color:#333">Brenhall</span>
      <div class="abs clients-arrow" style="left:876px">
        <svg width="10" height="14" viewBox="0 0 10 14"><path d="M2 1l6 6-6 6" fill="none" stroke="#fff" stroke-width="3"/></svg>
      </div>
    </div>
  </section>

  <footer class="abs footer">
    <div class="abs region" style="left:26px;top:28px">
      <h2>Europe</h2>
      <ul>
        <li>17 Harrow Row</li>
        <li>Kelsmoor, KM4 2ZT</li>
        <li>Phone:+44(0)1632 960418</li>
        <li>Email:eu@corvinsoft.example</li>
      </ul>
    </div>
    <div class="abs region" style="left:278px;top:28px">
      <h2>North America</h2>
      <ul>
        <li>4100 Larkfield Ave, Suite 210</li>
        <li>Dunmore, TX 75590</li>
        <li>Phone:(555) 014 2290</li>
        <li>Email:us@corvinsoft.example</li>
      </ul>
    </div>
    <span class="abs divider"></span>
    <div class="abs feedback" style="left:546px;top:20px">
      <h2>Customer Feedback</h2>
    </div>
    <div class="abs field" style="left:550px;top:46px;width:140px;height:29px">Name</div>
    <div class="abs field" style="left:701px;top:46px;width:140px;height:29px">Email</div>
    <div class="abs field" style="left:550px;top:81px;width:291px;height:84px">Type your message here</div>
  </footer>

  <div class="abs base">
    <a>Home</a><a>News</a><a>About Us</a><a>Solutions</a><a>Contact Us</a>
    <span class="copy">Copyright © Corvinsoft 2013 All Rights Reserved</span>
  </div>

</div>
</body>
</html>
```